Explosive, chemical reaction of creativity!

Web design for a digital marketing company. The unconventional is encouraged!
This is for a cool, young, geographically diverse company (sketchhive... you are all part of our team!!!)... we build websites but our real specialty is "search experience optimization".... creating conversion focused content, SEO (including content), and social media.

Target Market(s)

small to medium size businesses, law firms, medical practices, municipalities

Industry/Entity Type

Marketing

Number of Pages Required

2 page

Requirements
Must have
• WOW
• something different and special... we've been playing with a science theme (www.fernquillmedia.marketing) but we are open to different looks, layouts, etc.
• we nee a homepage design and an interior page design
• content needs to include: Marketing Catalysts (about us), Our Formula (services), Chemical Reactions(Results/Our Clients),
• FREE Online Prism Check
• Let us put together an objective snapshot of your digital presence for you.
Nice to have
• we are open to the use of background video (chemical reaction???)
• we are open to cool and different imagery
Should not have
• template look like most other websites

```html
<!DOCTYPE html>
<html lang="en">
<head>
<meta charset="utf-8">
<title>Fernquill Media Marketing</title>
<link href="https://fonts.googleapis.com/css2?family=Roboto:wght@300;400;500;700&display=swap" rel="stylesheet">
<style>
:root{
  --blue:#2a6ebb;
  --blue-dark:#1b4f8c;
  --navy:#0f2744;
  --ink:#333a44;
  --muted:#7d8591;
  --light:#eeeeee;
  --white:#ffffff;
  --dark:#24282d;
  --darker:#16191c;
}
*{box-sizing:border-box;margin:0;padding:0}
html,body{width:1200px;height:3112px;overflow:hidden}
body{font-family:'Roboto',sans-serif;color:var(--ink);background:var(--white);position:relative}
section,header,footer{position:absolute;left:0;width:1200px}
.btn{display:inline-block;background:var(--blue);color:var(--white);font-size:12px;font-weight:500;letter-spacing:1px;padding:10px 20px;border-radius:3px}
.btn.ghost{background:transparent;border:2px solid var(--white)}
.read-more{color:var(--blue);font-size:11px;font-weight:700;letter-spacing:1px;border-bottom:1px solid var(--blue);padding-bottom:2px}
.section-title{text-align:center;color:var(--blue);font-size:28px;font-weight:500;letter-spacing:1px}
.title-rule{width:60px;height:3px;background:var(--blue);margin:14px auto 0}

/* top bar */
.topbar{top:0;height:32px;background:var(--navy);color:#c9d6e6;font-size:12px;display:flex;align-items:center;gap:26px;padding-left:130px}
.topbar span{display:flex;align-items:center;gap:6px}
/* nav */
.nav{top:32px;height:88px;background:var(--white);display:flex;align-items:center;justify-content:space-between;padding:0 130px;box-shadow:0 1px 4px rgba(0,0,0,.08)}
.brand{display:flex;align-items:center;gap:10px;font-size:22px;font-weight:700;color:var(--blue-dark);letter-spacing:1px}
.brand-mark{width:22px;height:22px;background:var(--blue-dark)}
.menu{display:flex;gap:34px;font-size:12px;font-weight:500;letter-spacing:.5px}
.menu a{color:var(--ink);text-decoration:none}
.menu a.active{color:var(--blue)}
/* hero */
.hero{top:120px;height:420px;background:linear-gradient(110deg,#2f5d93 0%,#7fa9d4 40%,#dce9f5 70%,#a9c6e3 100%)}
.hero-copy{position:absolute;left:130px;top:110px;color:var(--white)}
.hero-copy h1{font-size:44px;font-weight:700;line-height:1.15}
.hero-copy p{font-size:14px;margin:14px 0 28px;width:380px;opacity:.9}
.hero .arrow{position:absolute;top:190px}
.dots{position:absolute;bottom:22px;left:0;width:100%;display:flex;justify-content:center;gap:8px}
.dots i{width:10px;height:10px;border-radius:50%;background:rgba(255,255,255,.5)}
.dots i:first-child{background:var(--white)}
/* welcome */
.welcome{top:540px;height:260px;text-align:center;padding-top:66px}
.welcome p{width:920px;margin:22px auto 26px;font-size:13px;line-height:1.7;color:var(--muted)}
/* prism check */
.prism{top:800px;height:400px;background:var(--light)}
.prism-copy{position:absolute;left:130px;top:70px;width:520px}
.prism-copy h2{color:var(--blue);font-size:28px;font-weight:500;margin-bottom:20px}
.prism-copy p{font-size:13px;line-height:1.7;color:var(--muted);margin-bottom:16px}
.prism-device{position:absolute;left:760px;top:40px;width:190px;height:330px;border-radius:22px;background:linear-gradient(160deg,#2b3038,#0d0f12)}
/* stats */
.stats{top:1200px;height:220px;background:linear-gradient(120deg,#1c2430,#3b4654 55%,#1e2630)}
.stat{position:absolute;top:42px;width:180px;text-align:center;color:var(--white)}
.stat strong{display:block;font-size:32px;font-weight:700;margin-top:10px}
.stat small{display:block;font-size:11px;line-height:1.5;opacity:.8;margin-top:6px}
/* formula */
.formula{top:1420px;height:440px;padding-top:50px}
.service{position:absolute;top:160px;width:260px;text-align:center}
.service .circle{width:96px;height:96px;border-radius:50%;background:var(--blue);margin:0 auto 22px;display:flex;align-items:center;justify-content:center}
.service h3{color:var(--blue);font-size:16px;font-weight:700;letter-spacing:1px;margin-bottom:12px}
.service p{font-size:12px;line-height:1.7;color:var(--muted);margin-bottom:14px}
/* snapshot band */
.snapshot{top:1860px;height:320px;background:linear-gradient(100deg,#0e4fa3,#2f7fd6 50%,#155db8)}
.snapshot-copy{position:absolute;left:200px;top:70px;width:800px;text-align:center;color:var(--white)}
.snapshot-copy h2{font-size:16px;font-weight:500;letter-spacing:1px}
.snapshot-copy p{font-size:12px;line-height:1.7;opacity:.85;margin:12px 0 30px}
/* news */
.news{top:2180px;height:500px;padding-top:50px}
.post{position:absolute;top:160px;width:280px}
.post-image{width:280px;height:140px}
.post h3{color:var(--blue);font-size:20px;font-weight:700;margin:18px 0 4px}
.post time{font-size:11px;color:var(--muted)}
.post p{font-size:12px;line-height:1.6;color:var(--muted);margin:10px 0 14px}
/* contact */
.contact{top:2680px;height:360px;background:linear-gradient(180deg,#2b3036,#1d2125);color:var(--white)}
.contact h2{text-align:center;font-size:30px;font-weight:400;padding-top:40px}
.contact .lead{text-align:center;font-size:12px;opacity:.7;margin-top:4px}
.field{position:absolute;font-size:12px;opacity:.85}
.field .box{margin-top:6px;border:1px solid rgba(255,255,255,.35);background:rgba(255,255,255,.05);height:32px}
.info{position:absolute;left:740px;top:130px;font-size:12px;line-height:2.1;opacity:.9}
.info div{display:flex;align-items:center;gap:8px}
.social{display:flex;gap:14px;margin-top:14px;padding-left:26px}
.social i{width:18px;height:18px;border-radius:50%;background:rgba(255,255,255,.8)}
.submit{position:absolute;left:560px;top:296px}
/* footer */
.footer{top:3040px;height:72px;background:var(--darker);color:#8b929b;font-size:12px;display:flex;align-items:center;justify-content:center}
</style>
</head>
<body>

<header class="topbar">
  <span><svg width="12" height="12" viewBox="0 0 24 24"><path fill="#c9d6e6" d="M6.6 10.8a15 15 0 0 0 6.6 6.6l2.2-2.2c.3-.3.7-.4 1-.2 1.1.4 2.3.6 3.6.6.6 0 1 .4 1 1V20c0 .6-.4 1-1 1A17 17 0 0 1 3 4c0-.6.4-1 1-1h3.5c.6 0 1 .4 1 1 0 1.3.2 2.5.6 3.6.1.3 0 .7-.2 1z"/></svg>(555) 014-2290</span>
  <span><svg width="12" height="12" viewBox="0 0 24 24"><path fill="#c9d6e6" d="M12 2a7 7 0 0 0-7 7c0 5 7 13 7 13s7-8 7-13a7 7 0 0 0-7-7zm0 9.5A2.5 2.5 0 1 1 12 6.5a2.5 2.5 0 0 1 0 5z"/></svg>88 Quarry Lane, Suite 12, Alderbrook, CO 80234</span>
</header>

<header class="nav">
  <div class="brand"><span class="brand-mark"></span>FERNQUILL MEDIA</div>
  <nav class="menu">
    <a class="active">HOME</a><a>MARKETING CATALYSTS</a><a>OUR FORMULA</a><a>CHEMICAL REACTIONS</a><a>CONTACT US</a>
  </nav>
</header>

<section class="hero" role="img" aria-label="Laboratory glassware with blue liquid in a bright lab">
  <svg class="arrow" style="left:40px" width="20" height="40" viewBox="0 0 20 40"><path d="M16 4 4 20l12 16" fill="none" stroke="#fff" stroke-width="3"/></svg>
  <svg class="arrow" style="right:40px" width="20" height="40" viewBox="0 0 20 40"><path d="M4 4l12 16L4 36" fill="none" stroke="#fff" stroke-width="3"/></svg>
  <div class="hero-copy">
    <h1>Fernquill Media<br>science!</h1>
    <p>Where curious minds mix data, design and content into results that keep growing for you.</p>
    <span class="btn">READ MORE</span>
  </div>
  <div class="dots"><i></i><i></i><i></i></div>
</section>

<section class="welcome">
  <h2 class="section-title">WELCOME TO FERNQUILL MEDIA MARKETING</h2>
  <p>We are a young and curious team spread across many places, building websites with a real specialty in search experience optimization. We create conversion focused content, strong SEO and lively social media that helps small and medium businesses, law firms, medical practices and municipalities grow in a measurable way.</p>
  <span class="btn">READ MORE</span>
</section>

<section class="prism">
  <div class="prism-copy">
    <h2>FREE ONLINE PRISM CHECK</h2>
    <p>Curious how your business looks online? Our free check takes a close look at your website, search rankings, content and social profiles, then shows you where the real opportunities are hiding.</p>
    <p>Send us your details and our team will put together a clear report with next steps you can use today.</p>
    <span class="btn">READ MORE</span>
  </div>
  <div class="prism-device" role="img" aria-label="Smartphone showing the company mark on its screen"></div>
</section>

<section class="stats" role="img" aria-label="Dark workspace photo behind key results">
  <div class="stat" style="left:190px">
    <svg width="34" height="34" viewBox="0 0 24 24"><rect x="7" y="2" width="10" height="20" rx="2" fill="none" stroke="#fff" stroke-width="1.6"/><circle cx="12" cy="18.5" r="1" fill="#fff"/></svg>
    <strong>70%</strong><small>of local searches on mobile lead to a call or visit</small>
  </div>
  <div class="stat" style="left:390px">
    <svg width="34" height="34" viewBox="0 0 24 24"><rect x="4" y="2" width="16" height="20" rx="2" fill="none" stroke="#fff" stroke-width="1.6"/><circle cx="12" cy="19" r="1" fill="#fff"/></svg>
    <strong>70%</strong><small>of buyers research online before they pick a provider</small>
  </div>
  <div class="stat" style="left:598px">
    <svg width="34" height="34" viewBox="0 0 24 24"><path d="M12 2 5 11h4l-5 7h7v4h2v-4h7l-5-7h4z" fill="#fff"/></svg>
    <strong>70%</strong><small>of clicks go to organic results over paid ads</small>
  </div>
  <div class="stat" style="left:810px">
    <svg width="34" height="34" viewBox="0 0 24 24"><rect x="5" y="2" width="14" height="20" rx="1" fill="none" stroke="#fff" stroke-width="1.6"/><path d="M8 7h8M8 11h8M8 15h5" stroke="#fff" stroke-width="1.6"/></svg>
    <strong>50%</strong><small>of companies still lack a clear content plan</small>
  </div>
</section>

<section class="formula">
  <h2 class="section-title">OUR FORMULA</h2>
  <div class="title-rule"></div>
  <div class="service" style="left:140px">
    <div class="circle"><svg width="44" height="44" viewBox="0 0 24 24" fill="none" stroke="#fff" stroke-width="1.5"><circle cx="12" cy="12" r="9"/><ellipse cx="12" cy="12" rx="4" ry="9"/><path d="M3 12h18"/></svg></div>
    <h3>WEBSITE</h3>
    <p>Fast, clean websites built to turn visitors into leads, shaped around how your customers really search and decide.</p>
    <span class="read-more">READ MORE</span>
  </div>
  <div class="service" style="left:470px">
    <div class="circle"><svg width="44" height="44" viewBox="0 0 24 24" fill="none" stroke="#fff" stroke-width="1.5"><rect x="3" y="4" width="18" height="12" rx="1"/><path d="M9 20h6M12 16v4"/></svg></div>
    <h3>CONTENT</h3>
    <p>Useful, search friendly content that answers real questions, earns trust and keeps people coming back for more.</p>
    <span class="read-more">READ MORE</span>
  </div>
  <div class="service" style="left:800px">
    <div class="circle"><svg width="44" height="44" viewBox="0 0 24 24" fill="#fff"><circle cx="12" cy="8" r="3"/><path d="M6 20a6 6 0 0 1 12 0z"/><circle cx="5" cy="10" r="2"/><circle cx="19" cy="10" r="2"/></svg></div>
    <h3>SOCIAL</h3>
    <p>Social media that sparks conversation, grows your audience and links your brand to the people who need it most.</p>
    <span class="read-more">READ MORE</span>
  </div>
</section>

<section class="snapshot" role="img" aria-label="Blue molecular structure and formula background">
  <div class="snapshot-copy">
    <h2>LET US PUT TOGETHER AN OBJECTIVE SNAPSHOT OF YOUR DIGITAL PRESENCE FOR YOU</h2>
    <p>We review your website, rankings, reviews, content and social channels, then turn everything we find into a simple picture of where you stand today and which steps will bring the biggest lift for your business.</p>
    <span class="btn ghost">READ MORE</span>
  </div>
</section>

<section class="news">
  <h2 class="section-title">RECENT NEWS</h2>
  <div class="title-rule"></div>
  <article class="post" style="left:140px">
    <div class="post-image" role="img" aria-label="Scientist working with test tubes" style="background:linear-gradient(135deg,#cfe0f2,#8fb4da)"></div>
    <h3>LOREM IPSUM DOLOR</h3><time>MAY 10, 2016</time>
    <p>Fresh ideas on search, content and social, with simple tips you can try this week to reach more local customers.</p>
    <span class="read-more">READ MORE</span>
  </article>
  <article class="post" style="left:460px">
    <div class="post-image" role="img" aria-label="Rows of lab flasks" style="background:linear-gradient(135deg,#e8d8c8,#b99a7c)"></div>
    <h3>LOREM IPSUM DOLOR</h3><time>MAY 10, 2016</time>
    <p>How a clear content plan helped a small practice double its leads in six months without adding ad spend.</p>
    <span class="read-more">READ MORE</span>
  </article>
  <article class="post" style="left:780px">
    <div class="post-image" role="img" aria-label="Blue glassware on a lab bench" style="background:linear-gradient(135deg,#d6e6f5,#5f8fc4)"></div>
    <h3>LOREM IPSUM DOLOR</h3><time>MAY 10, 2016</time>
    <p>Five quick checks to see if your website is ready for mobile visitors and the way people search today.</p>
    <span class="read-more">READ MORE</span>
  </article>
</section>

<section class="contact">
  <h2>Contact us</h2>
  <p class="lead">We would love to hear from you</p>
  <label class="field" style="left:170px;top:130px;width:210px">Name<div class="box"></div></label>
  <label class="field" style="left:170px;top:190px;width:210px">Email<div class="box"></div></label>
  <label class="field" style="left:170px;top:250px;width:210px">Phone Number<div class="box"></div></label>
  <label class="field" style="left:400px;top:130px;width:290px">Message<div class="box" style="height:152px"></div></label>
  <div class="info">
    <div><svg width="14" height="14" viewBox="0 0 24 24"><path fill="#fff" d="M12 2a7 7 0 0 0-7 7c0 5 7 13 7 13s7-8 7-13a7 7 0 0 0-7-7z"/></svg>88 Quarry Lane</div>
    <div style="padding-left:22px">Suite 12</div>
    <div style="padding-left:22px">Alderbrook, CO 80234</div>
    <div><svg width="14" height="14" viewBox="0 0 24 24"><path fill="#fff" d="M3 5h18v14H3zm2 2v.5l7 5 7-5V7z"/></svg>hello@fernquillmedia.marketing</div>
    <div><svg width="14" height="14" viewBox="0 0 24 24"><path fill="#fff" d="M6.6 10.8a15 15 0 0 0 6.6 6.6l2.2-2.2c.3-.3.7-.4 1-.2 1.1.4 2.3.6 3.6.6.6 0 1 .4 1 1V20c0 .6-.4 1-1 1A17 17 0 0 1 3 4c0-.6.4-1 1-1h3.5c.6 0 1 .4 1 1 0 1.3.2 2.5.6 3.6.1.3 0 .7-.2 1z"/></svg>(555) 014-2290</div>
    <div class="social"><i></i><i></i><i></i></div>
  </div>
  <span class="btn submit">Submit</span>
</section>

<footer class="footer">Copyright © 2016, Fernquill Media Marketing. All Rights Reserved.</footer>

</body>
</html>
```